Computer Training in the Education sector - Letterhead

We need a new letter head to be designed for the company. We provide computer training fro the Education Sector, both primary and private tertiary providers. The colours will need to tie in with the website www.crossingthestream.co.nz.
The company name is Crossing the Stream with the tag line of Computer Training for Educators.
The footer will need to have the following detail...
0508 PCS MENTOR
021 839 415
www.crossingthestream.co.nz / training@crossingthestream.co.nz
Updates

Thanks for the designs so far.

Some have watermarks in the background. Please don't worry about using watermarks as I will not be using a watermark in in a final design.
Regards,
Roger

Thank you for all the designs and the effort. There was some great concepts that came through.

Cheers
Roger

Industry/Entity Type

Computer

```html
<!DOCTYPE html>
<html lang="en">
<head>
<meta charset="utf-8">
<title>Crossing the Stream – Letterhead</title>
<link rel="stylesheet" href="https://fonts.googleapis.com/css2?family=Tinos:wght@400;700&display=swap">
<style>
  :root {
    --paper: #ffffff;
    --brand-blue: #2a7fe3;
    --brand-green: #86e02a;
    --brand-orange: #ee8530;
    --footer-text: #ffffff;
  }
  html, body {
    margin: 0;
    padding: 0;
    width: 848px;
    height: 1200px;
    overflow: hidden;
    background: var(--paper);
  }
  .letterhead {
    position: relative;
    width: 848px;
    height: 1200px;
    background: var(--paper);
    font-family: "Tinos", "Times New Roman", serif;
  }
  .brand {
    position: absolute;
    top: 44px;
    right: 62px;
    display: flex;
    align-items: center;
    gap: 12px;
  }
  .brand-dot {
    width: 22px;
    height: 22px;
    border-radius: 50%;
    background: var(--brand-orange);
    flex: none;
  }
  .brand-name {
    margin: 0;
    font-size: 34px;
    font-weight: 400;
    line-height: 1.05;
    color: var(--brand-blue);
    text-align: right;
  }
  .brand-url {
    position: absolute;
    top: 180px;
    right: 60px;
    margin: 0;
    font-size: 14px;
    font-weight: 700;
    letter-spacing: 0.3px;
    color: var(--brand-blue);
  }
  .footer-waves {
    position: absolute;
    left: 0;
    top: 0;
    width: 848px;
    height: 1200px;
  }
  .footer-contact {
    position: absolute;
    left: 596px;
    top: 1100px;
    margin: 0;
    padding: 0;
    list-style: none;
    font-size: 14px;
    line-height: 25px;
    letter-spacing: 0.4px;
    color: var(--footer-text);
  }
</style>
</head>
<body>
<main class="letterhead">
  <header class="brand">
    <span class="brand-dot"></span>
    <h1 class="brand-name">Crossing<br>the Stream</h1>
  </header>
  <p class="brand-url">www.crossingthestream.co.nz</p>

  <svg class="footer-waves" viewBox="0 0 848 1200" aria-hidden="true">
    <path fill="var(--brand-orange)" d="M0 1106 C200 1070 380 1010 560 1016 C700 1020 790 1045 848 1059 L848 1200 L0 1200 Z"/>
    <path fill="var(--brand-green)" d="M0 1122 C200 1090 400 1032 580 1040 C720 1046 800 1068 848 1079 L848 1200 L0 1200 Z"/>
    <path fill="var(--brand-blue)" d="M0 1140 C220 1110 420 1055 600 1062 C730 1067 800 1090 848 1100 L848 1200 L0 1200 Z"/>
  </svg>

  <ul class="footer-contact">
    <li>training@crossingthestream.co.nz</li>
    <li>0508 PCS MENTOR</li>
    <li>021 839 415</li>
  </ul>
</main>
</body>
</html>
```